Business Cards for IT Consulting Company (Managed Service Provider)

I am looking to have some business cards printed and would like some designs. We are an IT Consulting company based in Vancouver BC. I would like a nice clean and modern look to the cards. I have uploaded all the versions of my logo so parts can be used as needed. Here is a snippit from our website homepage:

Quillbrook Networks Ltd. is an IT Solutions Partner located in Vancouver BC, Canada. We offer IT solutions and support to customers in the greater Vancouver Area. With expertise in Microsoft platforms, as well as Linux and Mac OSX and over 12 years experience in the IT industry, Quillbrook Networks is dedicated to offering our clients top quality service and products. We take pride in the solutions we offer our customers. The greatest compliment a client can give us is to recommend our services.

Quillbrook Networks Ltd. offers a wide range of IT services from onsite service to remote support and managed service solutions. This allows clients to choose the support path that best suits their company’s needs. Supporting many different sized companies from small to enterprise level over the past 12 years Quillbrook Networks has the experience and expertise needed to ensure things run smoothly. Allowing our clients to focus on doing business.

Revolutionizing the way IT services are delivered.

Quillbrook Networks is dedicated to providing our clients with IT solutions that work and grow with them for years to come. This philosophy helps save money in the long run instead of replacing equipment constantly. Far too often IT solutions are not well thought out and while possibly solving the problem at hand, require replacement due to growth or quality within a very short time frame. Quillbrook Networks takes pride in providing solutions that will last and be able to accommodate growth without the need for replacement.

Industry/Entity Type

Information Technology

Contact Information for Business Card

Quillbrook Networks Ltd.
(Employee Name)
Eml: (Employees Email Address)
Web: quillbrook.me
Ph: 604-555-0148

Font styles to use
Serif
Sans Serif

Requirements
Must have
• The Company logo and company colors.
Nice to have
• - Our tag line: "Revolutionizing IT Services" or "Revolutionizing the way IT services are delivered."
• - Also I really like the idea of nature and technology together blending which is sort of where my logo came from so integrating that somehow onto the business cards would be great.

```html
<!DOCTYPE html>
<html lang="en">
<head>
<meta charset="utf-8">
<title>Quillbrook Networks Ltd. – Business Card</title>
<link rel="stylesheet" href="https://fonts.googleapis.com/css2?family=Open+Sans:wght@400;600;700&display=swap">
<style>
  :root {
    --brand-blue: #00a9e8;
    --brand-blue-deep: #0a9fdc;
    --slate: #5d5f61;
    --paper: #ffffff;
    --backdrop: #eceff1;
    --ink-light: #ffffff;
  }
  * { margin: 0; padding: 0; box-sizing: border-box; }
  html, body {
    width: 1200px; height: 900px; overflow: hidden;
    background: var(--backdrop);
    font-family: "Open Sans", Arial, sans-serif;
  }
  .canvas { position: relative; width: 1200px; height: 900px; }

  .card { position: absolute; overflow: hidden; box-shadow: 0 6px 18px rgba(0,0,0,.18); }

  /* Front card */
  .card-front { left: 77px; top: 34px; width: 589px; height: 364px; background: var(--paper); }
  .card-front .bands { position: absolute; inset: 0; }
  .company-name {
    position: absolute; left: 120px; top: 48px;
    color: var(--brand-blue); font-weight: 600; line-height: 1;
  }
  .company-name .name-main { display: block; font-size: 52px; letter-spacing: -0.5px; }
  .company-name .name-sub { display: block; font-size: 19px; margin-top: 4px; letter-spacing: .5px; }
  .tagline {
    position: absolute; left: 208px; top: 138px;
    font-size: 15.5px; font-weight: 600; color: var(--slate); letter-spacing: .2px;
  }
  .tagline .accent { color: var(--brand-blue); }

  .contact-list {
    position: absolute; right: 296px; top: 257px;
    list-style: none; text-align: right; color: var(--ink-light);
    font-size: 15px; line-height: 24px;
  }
  .contact-list li { display: flex; align-items: center; justify-content: flex-end; gap: 9px; }
  .contact-list svg { width: 12px; height: 12px; flex: none; }
  .person-name {
    position: absolute; left: 318px; top: 270px;
    color: var(--ink-light); font-size: 21px; font-weight: 600;
  }

  /* Back card */
  .card-back { left: 388px; top: 505px; width: 567px; height: 352px; background: var(--brand-blue-deep); }
  .back-name {
    position: absolute; left: 0; right: 0; top: 130px; text-align: center;
    color: var(--ink-light); font-weight: 600; line-height: 1;
  }
  .back-name .name-main { display: block; font-size: 54px; letter-spacing: -0.5px; }
  .back-name .name-sub { display: block; font-size: 19px; margin-top: 4px; letter-spacing: .5px; }
</style>
</head>
<body>
<main class="canvas">

  <section class="card card-front" aria-label="Business card front">
    <svg class="bands" width="589" height="364" viewBox="0 0 589 364" aria-hidden="true">
      <polygon points="0,199 400,199 382,226 0,226" fill="#5d5f61"/>
      <polygon points="0,230 386,230 416,191 589,191 589,364 0,364" fill="#00a9e8"/>
    </svg>

    <div class="company-name">
      <span class="name-main">Quillbrook</span>
      <span class="name-sub">NETWORKS LTD.</span>
    </div>
    <p class="tagline"><span class="accent">REVOLUTIONIZING</span> IT SERVICES</p>

    <ul class="contact-list">
      <li>604-555-0148
        <svg viewBox="0 0 24 24" aria-hidden="true"><path fill="#fff" d="M6.6 10.8a15.1 15.1 0 0 0 6.6 6.6l2.2-2.2c.3-.3.7-.4 1-.2 1.1.4 2.3.6 3.6.6.6 0 1 .4 1 1V20c0 .6-.4 1-1 1A17 17 0 0 1 3 4c0-.6.4-1 1-1h3.5c.6 0 1 .4 1 1 0 1.3.2 2.5.6 3.6.1.3 0 .7-.2 1z"/></svg>
      </li>
      <li>info@quillbrook.me
        <svg viewBox="0 0 24 24" aria-hidden="true"><rect x="2" y="5" width="20" height="14" fill="#fff"/><path d="M2 5l10 8 10-8" fill="none" stroke="#00a9e8" stroke-width="2"/></svg>
      </li>
      <li>www.quillbrook.me
        <svg viewBox="0 0 24 24" aria-hidden="true"><circle cx="12" cy="12" r="10" fill="#fff"/><path d="M7 8c2 0 3 1 3 3s-2 2-2 4M15 5c-1 2 1 3 3 3M14 19c0-2 1-3 3-3" fill="none" stroke="#00a9e8" stroke-width="2"/></svg>
      </li>
    </ul>
    <p class="person-name">Daniel Whitford</p>
  </section>

  <section class="card card-back" aria-label="Business card back">
    <div class="back-name">
      <span class="name-main">Quillbrook</span>
      <span class="name-sub">NETWORKS LTD.</span>
    </div>
  </section>

</main>
</body>
</html>
```